International Business Development Firm, in need of Branded Stationery material

We just made our Logo and now we are looking for branded stationery for our company such as:

* A Letterhead with our company's name, address, and logo at the top in Word format for easy editing
* A more formal letter format with a light background design (watermark) featuring our logo, allowing us to write over it for various documents and presentations
* Business card + Envelopes are a plus but not a must
* PowerPoint for company and product introductions
* An Info sheet with Bullet Points

The design should be professional.
Please ensure the design is high quality and print ready.

Target Market(s)

Businesses and high net value individuels

Industry/Entity Type

International Business Development Firm

Colors

Designer to choose colors to be used in the design.

Requirements
Must have
• word docs so i can use the stationery templates afterwards

```html
<!DOCTYPE html>
<html lang="en">
<head>
<meta charset="utf-8">
<title>Lumora Partners – Stationery</title>
<link rel="stylesheet" href="https://fonts.googleapis.com/css2?family=Lato:wght@400;700&family=Great+Vibes&display=swap">
<style>
  :root{
    --purple:#6a3d8f;
    --purple-soft:#9b82b8;
    --ink:#222222;
    --paper:#ffffff;
    --backdrop:#f1f1f3;
    --window-a:#e4e4e4;
    --window-b:#9a9a9a;
  }
  *{box-sizing:border-box;margin:0;padding:0}
  html,body{width:1200px;height:824px;overflow:hidden}
  body{background:var(--backdrop);font-family:"Lato",sans-serif;color:var(--ink);position:relative}
  .piece{position:absolute;background:var(--paper)}

  /* brand wordmark */
  .wordmark{position:absolute;color:var(--purple);font-weight:700;line-height:1}
  .wordmark .name{display:block}
  .wordmark .sub{display:block;letter-spacing:.42em}
  .wordmark.light{color:#fff}

  /* letterhead */
  .letterhead{left:128px;top:101px;width:446px;height:631px}
  .letterhead .wordmark{left:22px;top:36px}
  .letterhead .wordmark .name{font-size:24px}
  .letterhead .wordmark .sub{font-size:10px;margin-top:5px;margin-left:2px}
  .contact-rule{position:absolute;left:315px;top:26px;width:1px;height:54px;background:var(--purple)}
  .contact{position:absolute;left:327px;top:25px;font-size:8.6px;line-height:9.8px}
  .contact .gap{height:5px}
  .contact-line{display:flex;align-items:center;gap:3px}
  .icon{width:6px;height:6px;flex:none}
  .letter{position:absolute;left:22px;top:144px;width:401px;font-size:9.1px;line-height:9.9px}
  .letter .date{margin-bottom:11px}
  .letter .block{margin-bottom:11px}
  .letter .salute{font-size:11.6px;font-weight:700;margin:6px 0 13px}
  .letter p.body{text-align:justify;margin-bottom:10px}
  .letter .regards{margin-top:18px}
  .signature{font-family:"Great Vibes",cursive;font-size:22px;margin-top:42px}

  /* business cards */
  .card{top:101px;width:214px;height:122px;border-radius:8px;overflow:hidden}
  .card-front{left:639px}
  .card-front .wordmark{left:10px;top:13px}
  .card-front .wordmark .name{font-size:11px}
  .card-front .wordmark .sub{font-size:5px;margin-top:2px}
  .holder{position:absolute;left:8px;top:47px;border-left:4px solid var(--purple);padding-left:4px}
  .holder .person{font-size:8.5px;font-weight:700;color:var(--purple);line-height:9px}
  .holder .role{font-size:5.4px;color:var(--purple-soft);letter-spacing:.02em}
  .card-front .details{position:absolute;left:8px;top:72px;font-size:5.6px;line-height:7.6px}
  .card-front .details .gap{height:6px}
  .card-front .icon{width:4.5px;height:4.5px}
  .card-back{left:870px;background:var(--purple)}
  .card-back .wordmark{left:0;right:0;top:45px;text-align:center}
  .card-back .wordmark .name{font-size:22px}
  .card-back .wordmark .sub{font-size:8px;margin-top:4px}

  /* envelope back */
  .envelope-back{left:629px;top:279px;width:455px;height:200px}
  .flap{position:absolute;left:0;top:0;width:100%;height:58px;background:var(--purple-soft);border-radius:0 0 30px 30px}
  .flap .wordmark{left:0;right:0;top:22px;text-align:center;font-size:11px;letter-spacing:.08em}

  /* envelope front */
  .envelope-front{left:629px;top:534px;width:455px;height:198px}
  .envelope-front .wordmark{left:23px;top:28px}
  .envelope-front .wordmark .name{font-size:22px}
  .envelope-front .wordmark .sub{font-size:9px;margin-top:4px}
  .return-address{position:absolute;left:60px;top:71px;width:80px;text-align:center;font-size:7.4px;line-height:10.6px}
  .address-window{position:absolute;left:23px;top:132px;width:93px;height:36px;background:linear-gradient(135deg,var(--window-a) 0%,var(--window-a) 35%,var(--window-b) 55%,var(--window-a) 72%,#f0f0ee 100%)}
</style>
</head>
<body>

<svg width="0" height="0" style="position:absolute">
  <defs>
    <symbol id="i-phone" viewBox="0 0 10 10"><path d="M2 1l2 2-1 1.2c.6 1.2 1.6 2.2 2.8 2.8L7 6l2 2-1.3 1.3C4.5 9 1 5.5.7 2.3z" fill="#6a3d8f"/></symbol>
    <symbol id="i-mail" viewBox="0 0 10 10"><rect x="1" y="2.5" width="8" height="5.5" fill="none" stroke="#6a3d8f" stroke-width="1.2"/><path d="M1 2.5l4 3 4-3" fill="none" stroke="#6a3d8f" stroke-width="1.1"/></symbol>
    <symbol id="i-web" viewBox="0 0 10 10"><circle cx="5" cy="5" r="4" fill="#6a3d8f"/><path d="M1 5h8M5 1c-2 2.5-2 5.5 0 8M5 1c2 2.5 2 5.5 0 8" stroke="#fff" stroke-width=".7" fill="none"/></symbol>
  </defs>
</svg>

<section class="piece letterhead">
  <div class="wordmark"><span class="name">LUMORA</span><span class="sub">PARTNERS</span></div>
  <div class="contact-rule"></div>
  <div class="contact">
    <div>Your address, City</div>
    <div>State, Zip 1234</div>
    <div class="gap"></div>
    <div class="contact-line"><svg class="icon"><use href="#i-phone"/></svg>123 456 789</div>
    <div class="contact-line"><svg class="icon"><use href="#i-mail"/></svg>info@lumoramail.com</div>
    <div class="contact-line"><svg class="icon"><use href="#i-web"/></svg>www.lumorapartners.com</div>
  </div>
  <div class="letter">
    <div class="date">January-03-2020</div>
    <div class="block">Mr, Peter Lang<br>President</div>
    <div class="block">Northway Group<br>123 Street Name, Suite# 10<br>City, State, 120023</div>
    <div class="salute">Dear Mr, Peter</div>
    <p class="body">Lorem ipsum dolor sit amet, consectetur adipiscing elit, sed do eiusmod tempor incididunt ut labore et dolore magna aliqua. Ut enim ad minim veniam, quis nostrud exercitation ullamco laboris nisi ut aliquip ex ea commodo consequat. Duis aute irure dolor in reprehenderit in voluptate velit esse cillum dolore eu fugiat nulla pariatur.</p>
    <p class="body">Lorem ipsum dolor sit amet, consectetur adipiscing elit, sed do eiusmod tempor incididunt ut labore et dolore magna aliqua. Ut enim ad minim veniam, quis nostrud exercitation ullamco laboris nisi ut aliquip ex ea commodo consequat. Duis aute irure dolor in reprehenderit in voluptate velit esse cillum dolore eu fugiat nulla pariatur.</p>
    <p class="body">Lorem ipsum dolor sit amet, consectetur adipiscing elit, sed do eiusmod tempor incididunt ut labore et dolore magna aliqua. Ut enim ad minim veniam, quis nostrud exercitation ullamco laboris nisi ut aliquip ex ea commodo consequat.</p>
    <p class="body">Excepteur sint occaecat cupidatat non proident, sunt in culpa qui officia deserunt mollit anim id est laborum. re et dolore magnam aliquam quaerat voluptatem.</p>
    <div class="regards">Regards</div>
    <div class="signature">Clara Voss</div>
  </div>
</section>

<section class="piece card card-front">
  <div class="wordmark"><span class="name">LUMORA</span><span class="sub">PARTNERS</span></div>
  <div class="holder">
    <div class="person">DANIEL REYES</div>
    <div class="role">MANAGING DIRECTOR</div>
  </div>
  <div class="details">
    <div>Your address, City</div>
    <div>State, Zip 1234</div>
    <div class="gap"></div>
    <div class="contact-line"><svg class="icon"><use href="#i-phone"/></svg>123 456 789</div>
    <div class="contact-line"><svg class="icon"><use href="#i-mail"/></svg>info@lumoramail.com</div>
    <div class="contact-line"><svg class="icon"><use href="#i-web"/></svg>www.lumorapartners.com</div>
  </div>
</section>

<section class="piece card card-back">
  <div class="wordmark light"><span class="name">LUMORA</span><span class="sub">PARTNERS</span></div>
</section>

<section class="piece envelope-back">
  <div class="flap"><div class="wordmark light">LUMORA</div></div>
</section>

<section class="piece envelope-front">
  <div class="wordmark"><span class="name">LUMORA</span><span class="sub">PARTNERS</span></div>
  <div class="return-address">Your address, City<br>State, Zip 1234</div>
  <div class="address-window" role="img" aria-label="Address window"></div>
</section>

</body>
</html>
```